Redesign of the current website

We would like a new format and redesign of the www.getvantoru.com website. We are a medical tech company and want our site to reflect current technology trends. VANTORU provides innovative solutions to streamline business operations of Imaging Providers and Physicians while delivering life-changing solutions to patients. Free to patients and physicians.

Target Market(s)

Imaging Providers (with a secondary appeal for physicians and patients)

Industry/Entity Type

MedTech

Coding

Coded - Design and coding required

Number of Pages Required

1 page

Font styles to use
Sans Serif

Requirements
Must have
• New clear slogan to represent who and what we do.
Nice to have
• VANTORU provides innovative solutions to streamline business operations of Imaging Providers and Physicians while delivering life-changing solutions to patients.
Should not have
• Bright Scanning or Join the revolution

```html
<!DOCTYPE html>
<html lang="en">
<head>
<meta charset="utf-8">
<title>VANTORU</title>
<link rel="stylesheet" href="https://fonts.googleapis.com/css2?family=Poppins:ital,wght@0,300;0,400;0,500;0,600;0,700;1,400&display=swap">
<style>
:root{
  --blue:#1793e3;
  --blue-dark:#0d5ea8;
  --navy:#0b2d55;
  --green:#6cbd35;
  --ink:#222;
  --text:#444;
  --muted:#777;
  --line:#cfd6dc;
  --news-bg:#e9f0f4;
  --foot-bar:#dce8ee;
  --white:#fff;
}
*{margin:0;padding:0;box-sizing:border-box}
html,body{width:1200px;height:4178px;overflow:hidden}
body{font-family:"Poppins",sans-serif;color:var(--ink);background:var(--white);position:relative}
.abs{position:absolute}
.btn{position:absolute;display:flex;align-items:center;justify-content:center;border-radius:30px;font-weight:600;font-size:14px;letter-spacing:.3px;text-transform:uppercase}
.btn-blue{background:var(--blue);color:var(--white)}
.btn-green{background:var(--green);color:var(--white)}
.btn-white{background:var(--white);color:var(--blue-dark)}
.rule{position:absolute;height:3px;width:60px;background:var(--blue)}
.section-title{position:absolute;left:0;width:1200px;text-align:center;font-size:36px;line-height:38px;font-weight:300;color:var(--ink)}
.section-title b{font-weight:700}

/* header */
.brand{position:absolute;left:124px;top:30px;font-size:40px;font-weight:700;color:var(--blue);letter-spacing:1px}
.brand-url{position:absolute;left:146px;top:88px;font-size:8px;color:var(--blue);letter-spacing:2px}
.call{position:absolute;left:800px;top:38px;font-size:12px;color:var(--blue);line-height:14px}
.call strong{display:block;font-size:17px;color:var(--navy);line-height:22px}
.nav{position:absolute;top:108px;left:0;width:1200px;height:56px;background:var(--blue)}
.nav a{position:absolute;color:var(--white);font-size:14px;font-weight:600;text-decoration:none;top:18px}
.nav .active::after{content:"";position:absolute;left:-6px;right:-6px;top:36px;height:3px;background:var(--green)}

/* hero */
.hero{position:absolute;top:164px;left:0;width:1200px;height:640px;background:linear-gradient(100deg,#0a3c5e 0%,#0e5a82 45%,#2b86b8 75%,#8fc2e0 100%)}
.hero h1{position:absolute;left:128px;top:170px;font-size:40px;line-height:50px;font-weight:700;color:var(--white);white-space:nowrap}
.hero p{position:absolute;left:132px;top:278px;width:410px;font-size:14px;line-height:22px;color:#e4eef6}
.dots{position:absolute;left:1151px;top:248px}
.dots i{display:block;width:12px;height:12px;border-radius:50%;background:var(--white);margin-bottom:10px}
.dots i.on{background:var(--green)}

/* intro */
.intro-frame{position:absolute;left:432px;top:955px;width:675px;height:425px;border:2px solid var(--line);border-radius:6px}
.intro-media{position:absolute;left:109px;top:987px;width:474px;height:349px;background:linear-gradient(135deg,#cfe6f7,#4aa0dc 60%,#1d6fb5)}
.intro-text{position:absolute;left:619px;top:1022px;width:452px;font-size:14px;line-height:23.5px;color:var(--text)}
.intro-text p{margin-bottom:10px}

/* empower */
.empower{position:absolute;top:1470px;left:0;width:1200px;height:560px;background:linear-gradient(90deg,#1a95e6,#1f8ee0)}
.empower h2{position:absolute;left:109px;top:140px;font-size:38px;line-height:40px;font-weight:700;color:var(--white);white-space:nowrap;z-index:2}
.empower h2 span{font-weight:300;display:block;font-size:35px}
.empower p{position:absolute;left:110px;top:245px;width:425px;font-size:14px;line-height:28px;color:#e8f3fb}
.empower-pic{position:absolute;left:545px;top:1430px;width:540px;height:540px;border-radius:50%;border:10px solid var(--white);background:radial-gradient(circle at 55% 45%,#7fc3f2,#1f6fc2 60%,#0b3e86)}

/* cost cards */
.cost-card{position:absolute;top:2242px;width:462px;height:320px;color:var(--white);text-align:center}
.cost-card h3{position:absolute;top:100px;width:100%;font-size:21px;line-height:26px;font-weight:500}
.cost-card p{position:absolute;top:162px;left:50px;width:362px;font-size:12px;line-height:15px;color:#dfeaf5}
.cost-card .btn{top:225px;left:166px;width:132px;height:36px;font-size:12px}

/* news */
.news{position:absolute;top:2685px;left:0;width:1200px;height:605px;background:var(--news-bg)}
.news h2{position:absolute;left:133px;top:38px;font-size:34px;font-weight:400;color:var(--ink)}
.news h2 b{font-weight:700}
.news-card{position:absolute;top:115px;width:311px;height:400px;background:var(--white);border:1px solid #d5dde2}
.news-card .thumb{height:216px}
.news-card h4{margin:28px 30px 0;font-size:17px;line-height:23px;font-weight:400;color:var(--ink)}
.news-card p{margin:14px 26px 0 30px;font-size:10.5px;line-height:16px;color:var(--text)}
.news-card .more{position:absolute;left:33px;top:348px;width:100px;height:25px;border:1.5px solid var(--blue);border-radius:14px;font-size:10px;color:var(--blue);display:flex;align-items:center;justify-content:center;font-weight:500}

/* reviews */
.reviews-title{position:absolute;top:3368px;left:0;width:1200px;text-align:center;font-size:36px;color:var(--white);font-weight:300}
.reviews-title b{font-weight:700}
.review{position:absolute;text-align:center;color:var(--white)}
.review .avatar{width:56px;height:56px;border-radius:50%;margin:0 auto;background:#c9b9a6}
.review h5{font-size:12px;font-weight:500;margin-top:12px}
.review p{font-style:italic;font-size:12px;line-height:19px;margin:8px auto 0;width:210px;color:#eaf6df}
.review.side{top:3470px;width:245px;height:230px;background:var(--green);box-shadow:0 4px 18px rgba(0,0,0,.15);padding-top:20px}
.review.main{top:3445px;left:451px;width:292px;height:280px;background:var(--white);box-shadow:0 6px 24px rgba(0,0,0,.18);padding-top:30px}
.review.main h5{color:var(--green);font-size:14px}
.review.main p{color:var(--muted);font-size:14px;line-height:22px;width:240px}

/* footer */
.foot-brand{position:absolute;left:152px;top:3895px;font-size:42px;font-weight:700;color:var(--green)}
.foot-url{position:absolute;left:198px;top:3960px;font-size:8px;letter-spacing:2px;color:var(--blue)}
.foot-col{position:absolute;top:3890px}
.foot-col h6{font-size:14px;font-weight:600;color:var(--blue);letter-spacing:.5px}
.foot-col h6::after{content:"";display:block;width:30px;height:2px;background:var(--green);margin-top:6px}
.foot-col ul{list-style:none;margin-top:14px;font-size:11.5px;line-height:25px;color:var(--text)}
.social{display:flex;gap:6px;margin-top:14px}
.social i{width:32px;height:32px;border-radius:50%;border:1.5px solid var(--blue);display:block}
.foot-bar{position:absolute;top:4110px;left:0;width:1200px;height:68px;background:var(--foot-bar);text-align:center;font-size:11px;line-height:68px;color:var(--text)}
</style>
</head>
<body>

<header>
  <div class="brand">VANTORU</div>
  <div class="brand-url">WWW.GETVANTORU.COM</div>
  <svg class="abs" style="left:766px;top:42px" width="24" height="26" viewBox="0 0 24 24" aria-hidden="true"><path d="M6.6 10.8a15.1 15.1 0 0 0 6.6 6.6l2.2-2.2c.3-.3.7-.4 1-.2 1.1.4 2.3.6 3.6.6.6 0 1 .4 1 1V20c0 .6-.4 1-1 1C10.6 21 3 13.4 3 4c0-.6.4-1 1-1h3.5c.6 0 1 .4 1 1 0 1.3.2 2.5.6 3.6.1.3 0 .7-.2 1z" fill="#1793e3"/></svg>
  <div class="call">CALL US NOW<strong>1-800-555-0142</strong></div>
  <div class="btn btn-green" style="left:958px;top:37px;width:162px;height:40px;font-size:12px">Register Now</div>
</header>

<nav class="nav">
  <a class="active" style="left:128px">HOME</a>
  <a style="left:228px">ABOUT US</a>
  <a style="left:358px">SOLUTION</a>
  <a style="left:490px">STORAGE</a>
  <a style="left:615px">NEWS ROOM</a>
  <a style="left:760px">PHYSICIAN GUEST ACCESS</a>
  <a style="left:1014px">CONTACT US</a>
</nav>

<section class="hero" role="img" aria-label="Hand holding a tablet showing a holographic body scan over a molecular background">
  <h1>Imaging Made Simple<br>free for everyone <span style="display:inline-block;width:60px;height:2px;background:#6cbd35;vertical-align:middle"></span></h1>
  <p>There are so many competing pressures on healthcare providers today; meaningful use, data security, managing costs and of course increasing revenue.</p>
  <div class="btn btn-blue" style="left:128px;top:361px;width:160px;height:44px">Learn More</div>
  <div class="dots"><i></i><i></i><i class="on"></i><i></i></div>
</section>
<svg class="abs" style="left:0;top:700px" width="1200" height="110" viewBox="0 0 1200 110" aria-hidden="true">
  <path d="M0 100 Q600 -10 1200 70 L1200 110 L0 110Z" fill="#6cbd35"/>
  <path d="M0 104 Q600 10 1200 85 L1200 110 L0 110Z" fill="#fff"/>
</svg>

<h2 class="section-title" style="top:820px">Smarter imaging, free for all!<br><b>Thinking Ahead</b></h2>
<div class="rule" style="left:570px;top:912px"></div>

<div class="intro-frame"></div>
<div class="intro-media" role="img" aria-label="Doctor using a tablet with floating medical icons">
  <svg class="abs" style="left:205px;top:142px" width="66" height="66" viewBox="0 0 66 66" aria-hidden="true"><circle cx="33" cy="33" r="31" fill="#fff"/><path d="M27 21 L46 33 L27 45Z" fill="#1793e3"/></svg>
</div>
<div class="intro-text">
  <p>There are so many competing pressures on healthcare providers today; meaningful use, data security, managing costs and of course increasing revenue.</p>
  <p>Solving all of these issues can sometimes seem like a mine field... what systems should I buy, how do I ensure data security while exposing it in patient or physician portals, how can I maintain or reduce my costs while meeting all of these requirements. VANTORU can help you meet these requirements through a revolutionary approach to the healthcare eco-system:</p>
</div>
<div class="btn btn-green" style="left:613px;top:1271px;width:165px;height:46px">Learn More</div>

<section class="empower">
  <h2>Empower Patients<span>&amp; Healthcare Providers</span></h2>
  <div class="abs" style="left:110px;top:222px;width:62px;height:3px;background:#fff"></div>
  <p>VANTORU allows the ownership of the images to be in the Patient's hands and enables interoperability between Diagnostic Imaging Centers, Patients and Physicians.</p>
  <div class="btn btn-white" style="left:106px;top:363px;width:178px;height:50px;font-size:15px">Learn More</div>
</section>
<div class="empower-pic" role="img" aria-label="Hand presenting a holographic human skeleton with organs, stethoscope and pills"></div>

<h2 class="section-title" style="top:2105px">Lower your costs white<br><b>streaming the diagnosis</b></h2>
<div class="rule" style="left:579px;top:2198px"></div>

<div class="cost-card" style="left:133px;background:linear-gradient(135deg,#0c2a5a,#123e78 60%,#0a2450)" role="img" aria-label="Data screens in dark blue tones">
  <h3>Streamlined Diagnosis<br>&amp; Decision Making</h3>
  <p>Diagnosis &amp; decision-making are streamlined. Hard copy production costs can now be eliminated with VANTORU's cloud-based service that is also PACS compatible.</p>
  <div class="btn btn-white">Learn More</div>
</div>
<div class="cost-card" style="left:612px;background:linear-gradient(135deg,#2c8de0,#1576d3 60%,#1263c0)" role="img" aria-label="Clinicians reviewing records in blue tones">
  <h3>Real-Time Access<br>to Historical Records</h3>
  <p>All participants now have real-time access to historical records &amp; business intelligence tools that eliminate overhead costs &amp; improve the quality of Patient Care.</p>
  <div class="btn btn-white">Learn More</div>
</div>

<section class="news">
  <h2>Latest <b>News</b></h2>
  <div class="rule" style="left:133px;top:85px"></div>
  <article class="news-card" style="left:129px">
    <div class="thumb" role="img" aria-label="Doctor holding a tablet with medical icons" style="background:linear-gradient(135deg,#eef4f9,#a9c9e6)"></div>
    <h4>Lorem ipsum dolor sit amet consectetur adipiscing elit</h4>
    <p>Excepteur sint occaecat cupidatat non proident, sunt in culpa qui officia deserunt molli</p>
    <div class="more">Learn More</div>
  </article>
  <article class="news-card" style="left:462px">
    <div class="thumb" role="img" aria-label="Hand touching a glowing digital medical cross" style="background:radial-gradient(circle at 55% 50%,#3fa7e0,#0b3a66 60%,#061f3c)"></div>
    <h4>Lorem ipsum dolor sit amet consectetur adipiscing elit</h4>
    <p>Excepteur sint occaecat cupidatat non proident, sunt in culpa qui officia deserunt molli</p>
    <div class="more">Learn More</div>
  </article>
  <article class="news-card" style="left:794px">
    <div class="thumb" role="img" aria-label="Radiologist reviewing scans on monitors" style="background:linear-gradient(135deg,#e9eef2,#8a97a3 60%,#2d3a46)"></div>
    <h4>Lorem ipsum dolor sit amet consectetur adipiscing elit</h4>
    <p>Excepteur sint occaecat cupidatat non proident, sunt in culpa qui officia deserunt molli</p>
    <div class="more">Learn More</div>
  </article>
</section>

<svg class="abs" style="left:0;top:3290px" width="1200" height="545" viewBox="0 0 1200 545" aria-hidden="true">
  <path d="M0 0 H1200 V470 Q600 590 0 480Z" fill="#6cbd35"/>
</svg>
<h2 class="reviews-title">Patient <b>Reviews</b></h2>
<div class="abs" style="left:570px;top:3422px;width:60px;height:3px;background:#fff"></div>
<svg class="abs" style="left:84px;top:3560px" width="24" height="40" viewBox="0 0 24 40" aria-hidden="true"><path d="M20 3 L4 20 L20 37" stroke="#fff" stroke-width="4" fill="none"/></svg>
<svg class="abs" style="left:1072px;top:3560px" width="24" height="40" viewBox="0 0 24 40" aria-hidden="true"><path d="M4 3 L20 20 L4 37" stroke="#fff" stroke-width="4" fill="none"/></svg>

<div class="review side" style="left:205px">
  <div class="avatar" role="img" aria-label="Reviewer portrait"></div>
  <h5>DEV MARLOWE</h5>
  <p>Etiam eu urna Sed porta Suspendisse quam leo molestie sed luctus quis feugiat in pede Fusce tellus Sed metus augue convallis</p>
</div>
<div class="review side" style="left:743px">
  <div class="avatar" role="img" aria-label="Reviewer portrait"></div>
  <h5>NINA CARROW</h5>
  <p>Etiam eu urna Sed porta Suspendisse quam leo molestie sed luctus quis feugiat in pede Fusce tellus Sed metus augue convallis</p>
</div>
<div class="review main">
  <div class="avatar" role="img" aria-label="Reviewer portrait" style="width:66px;height:66px"></div>
  <h5>PETER HOLM</h5>
  <p>Etiam eu urna Sed porta Suspendisse quam leo molestie sed luctus quis feugiat in pede Fusce tellus Sed metus augue convallis</p>
</div>

<footer>
  <div class="foot-brand">VANTORU</div>
  <div class="foot-url">WWW.GETVANTORU.COM</div>
  <div class="foot-col" style="left:397px">
    <h6>QUICK LINKS</h6>
    <ul style="display:grid;grid-template-columns:118px 100px"><li>About Us</li><li>Register</li><li>Solution</li><li>Services</li><li>Storage</li><li>Resources</li><li>News Room</li><li>Contact Us</li></ul>
  </div>
  <div class="foot-col" style="left:666px;top:3895px">
    <h6>INDUSTRY ARTICLES</h6>
    <ul><li>Imaging on Portals Saves Money</li><li>Images and Data on Internet</li><li>Benefits of patient portals</li><li>Handling Outside Imaging Studies</li><li>Radiologists improve shared decision-making</li></ul>
  </div>
  <div class="foot-col" style="left:945px;top:3895px">
    <h6>FOLLOW US</h6>
    <div class="social"><i></i><i></i><i></i><i></i></div>
  </div>
  <div class="foot-bar">© 2022 Company Name | All Rights Reserved</div>
</footer>

</body>
</html>
```